Business Card Design

New business card design

Target Market(s)

Residential & Commercial Property Managers

Industry/Entity Type

Plumbing Services

Contact Information for Business Card

Name - Rowan Keddle, title - Director, Phone Number - 0431 286 517, email - rowan@tbk-plumbing.com.au, Company ABN - 73 215 904 386,

Font styles to use
Sans Serif

Colors
0054AA
0677BA
7BADD7
CADEEF
E8F1F8

```html
<!DOCTYPE html>
<html lang="en">
<head>
<meta charset="utf-8">
<title>TBK Plumbing Services – Business Card</title>
<link href="https://fonts.googleapis.com/css2?family=Roboto:wght@300;400;700&display=swap" rel="stylesheet">
<style>
  :root {
    --blue-deep: #0054AA;
    --blue-mid: #0677BA;
    --blue-soft: #7BADD7;
    --blue-pale: #CADEEF;
    --blue-mist: #E8F1F8;
    --blue-bright: #1ea6e6;
    --stripe-grey: #6b625c;
    --ink: #1b1b1b;
    --ink-muted: #6a6a6a;
    --paper: #f7f7f7;
    --stage: #222222;
  }
  * { box-sizing: border-box; margin: 0; padding: 0; }
  html, body { width: 1200px; height: 852px; overflow: hidden; }
  body {
    background: var(--stage);
    font-family: "Roboto", Arial, sans-serif;
    position: relative;
  }
  .card {
    position: absolute;
    top: 271px;
    width: 540px;
    height: 310px;
    border-radius: 22px;
    overflow: hidden;
  }
  .card svg.card-art { position: absolute; inset: 0; width: 100%; height: 100%; }
  .card-front { left: 40px; }
  .card-back { left: 620px; background: var(--paper); }

  .brand {
    position: absolute;
    font-weight: 300;
    letter-spacing: 0.5px;
    white-space: nowrap;
  }
  .brand-front {
    color: #ffffff;
    left: 0; right: 0; top: 118px;
    text-align: center;
    font-size: 44px;
  }
  .brand-back {
    color: var(--ink);
    left: 34px; top: 94px;
    font-size: 30px;
  }

  .location {
    position: absolute;
    left: 34px; top: 180px;
    font-size: 13px;
    color: var(--ink);
  }
  .location .sep { color: var(--blue-bright); margin: 0 5px; }

  .social {
    position: absolute;
    left: 64px; top: 204px;
    display: flex; gap: 6px;
  }
  .social span {
    width: 20px; height: 20px; border-radius: 50%;
    background: var(--blue-mid);
  }
  .social span:first-child { background: var(--ink); }

  .holder {
    position: absolute;
    right: 34px; top: 24px;
    text-align: right;
  }
  .holder-name { font-size: 19px; font-weight: 700; color: var(--ink); }
  .holder-title { font-size: 12px; color: var(--ink-muted); margin-top: 1px; }

  .contact {
    position: absolute;
    right: 22px; top: 185px;
    list-style: none;
    color: #ffffff;
    font-size: 12px;
    font-weight: 300;
    line-height: 17px;
    text-align: right;
  }
  .contact li { display: flex; justify-content: flex-end; align-items: center; gap: 10px; }
  .contact svg { width: 11px; height: 11px; fill: var(--blue-bright); flex: none; }
</style>
</head>
<body>

  <section class="card card-front" aria-label="Card front">
    <svg class="card-art" viewBox="0 0 540 310" preserveAspectRatio="none">
      <defs>
        <linearGradient id="front-sky" x1="0" y1="0" x2="0" y2="1">
          <stop offset="0" stop-color="#3db0e0"/>
          <stop offset="1" stop-color="var(--blue-deep)"/>
        </linearGradient>
      </defs>
      <rect width="540" height="310" fill="url(#front-sky)"/>
      <path d="M0,90 C140,40 300,30 540,60 L540,310 L0,310 Z" fill="#1b8fcc" opacity="0.7"/>
      <path d="M0,170 C150,110 320,90 540,150 L540,310 L0,310 Z" fill="var(--blue-mid)" opacity="0.8"/>
      <path d="M0,240 C170,190 360,200 540,250 L540,310 L0,310 Z" fill="var(--blue-deep)" opacity="0.85"/>
    </svg>
    <div class="brand brand-front">TBK Plumbing Services</div>
  </section>

  <section class="card card-back" aria-label="Card back">
    <svg class="card-art" viewBox="0 0 540 310" preserveAspectRatio="none">
      <defs>
        <linearGradient id="back-wave" x1="0" y1="0" x2="1" y2="1">
          <stop offset="0" stop-color="#1a8fd0"/>
          <stop offset="1" stop-color="var(--blue-deep)"/>
        </linearGradient>
      </defs>
      <path d="M540,88 C440,95 390,130 350,180 C300,245 200,285 0,288 L0,310 L540,310 Z" fill="url(#back-wave)"/>
      <path d="M540,150 C480,170 450,210 410,240 C360,280 270,305 160,310 L540,310 Z" fill="var(--blue-deep)" opacity="0.5"/>
      <path d="M540,76 C436,84 382,122 340,172 C288,238 190,278 0,280" fill="none" stroke="var(--blue-bright)" stroke-width="5"/>
      <path d="M330,222 C280,268 190,292 0,296" fill="none" stroke="var(--stripe-grey)" stroke-width="7"/>
    </svg>

    <div class="holder">
      <p class="holder-name">Rowan Keddle</p>
      <p class="holder-title">Managing Director</p>
    </div>

    <div class="brand brand-back">TBK Plumbing Services</div>

    <p class="location">Sydney<span class="sep">|</span>NSW<span class="sep">|</span>Australia</p>

    <div class="social" aria-label="Social media"><span></span><span></span><span></span></div>

    <ul class="contact">
      <li>0431 286 517
        <svg viewBox="0 0 24 24" aria-hidden="true"><path d="M6.6 10.8c1.4 2.8 3.8 5.2 6.6 6.6l2.2-2.2c.3-.3.7-.4 1-.2 1.1.4 2.3.6 3.6.6.6 0 1 .4 1 1V20c0 .6-.4 1-1 1C10.6 21 3 13.4 3 4c0-.6.4-1 1-1h3.5c.6 0 1 .4 1 1 0 1.3.2 2.5.6 3.6.1.3 0 .7-.2 1z"/></svg>
      </li>
      <li>rowan@tbk-plumbing.com.au
        <svg viewBox="0 0 24 24" aria-hidden="true"><path d="M2 5h20v14H2z M4 7l8 6 8-6" fill="none" stroke="var(--blue-bright)" stroke-width="2.5"/></svg>
      </li>
      <li>www.tbk-plumbing.com.au
        <svg viewBox="0 0 24 24" aria-hidden="true"><circle cx="12" cy="12" r="9" fill="none" stroke="var(--blue-bright)" stroke-width="2.5"/><path d="M3 12h18M12 3c3 3 3 15 0 18M12 3c-3 3-3 15 0 18" fill="none" stroke="var(--blue-bright)" stroke-width="2"/></svg>
      </li>
      <li>ABN - 73 215 904 386
        <svg viewBox="0 0 24 24" aria-hidden="true"><path d="M9 3L7 21M17 3l-2 18M4 9h17M3 15h17" fill="none" stroke="var(--blue-bright)" stroke-width="2.5"/></svg>
      </li>
    </ul>
  </section>

</body>
</html>
```